Innovative coffee bean bag design for roasters

We need a design which can be printed on a coffee bean bag but which could also work on a sticker of similar size. We're after quirky, geeky, playful and innovative. Something that will stand out and communicate the character of our business. It should be eye catching and draw the customer in for a closer look.
Thematically, think organic and earthy.
It needs an element which can be changed for different coffee origins and roast profiles, so the main design will remain the same but with a feature which changes to help the customer know what they're looking at and will make them smile.
Approximate dimensions we need are 15cm by 12cm, with the 15cm being the vertical height of the bag image. (The image will be viewed in portrait). This is the main print area - however, if you have a great idea for a full bag image (approximately 23cm by 13cm), feel free to submit this too, we're interested in all ideas.
There is an image attached of a white partially see-through bag which we are considering using, so keep this in mind when designing.
We will need our logo including - see attached image.
Finally, we need space for the information about the coffee, such as origin, roast profile, flavour notes - see attached image for an example of the information (not necessarily a stylistic indicator). Please suggest fonts etc.

Target Market(s)

coffee roasters

Requirements
Must have
• Must say under the logo coffee roasters( Copper Kettle Organic Coffee Roasters )
Nice to have
• Unique symbol, shapes, scientific.

```html
<!DOCTYPE html>
<html lang="en">
<head>
<meta charset="utf-8">
<title>Brazilian Roast – Copper Kettle Organic Coffee Roasters</title>
<link rel="stylesheet" href="https://fonts.googleapis.com/css2?family=Josefin+Sans:wght@700&family=Mrs+Saint+Delafield&family=Nunito+Sans:wght@400;700;800&display=swap">
<style>
  :root {
    --red: #e34b2f;
    --peach: #f5c086;
    --green: #3c5e2b;
    --yellow: #f4c10f;
    --blue: #4079bf;
    --brown: #8b5a2f;
    --copper: #9a4f12;
    --ink: #1c1c1c;
    --paper: #ffffff;
    --backdrop: #f3f3f1;
  }
  * { margin: 0; padding: 0; box-sizing: border-box; }
  html, body {
    width: 1200px; height: 1167px; overflow: hidden;
    background: var(--backdrop);
  }
  .label {
    position: absolute; left: 308px; top: 43px;
    width: 584px; height: 1080px;
    background: var(--paper);
    box-shadow: 6px 8px 14px rgba(0,0,0,0.18);
    overflow: hidden;
    font-family: "Nunito Sans", sans-serif;
    color: var(--ink);
  }
  .colour-band {
    position: absolute; left: 0; top: 0; width: 584px; height: 559px;
    background: linear-gradient(90deg, var(--red) 0%, var(--yellow) 28%, var(--green) 52%, var(--blue) 76%, var(--brown) 100%);
  }

  .badge { position: absolute; left: 169px; top: 436px; width: 246px; height: 246px; }
  .badge-name {
    position: absolute; left: 194px; top: 500px; width: 196px;
    text-align: center;
    font-family: "Josefin Sans", sans-serif; font-weight: 700;
    font-size: 21px; line-height: 1.2; color: var(--copper);
  }

  .title {
    position: absolute; left: 0; width: 100%; top: 690px;
    text-align: center;
    font-family: "Josefin Sans", sans-serif; font-weight: 700;
    font-size: 50px; letter-spacing: 0.5px; line-height: 1;
  }
  .tagline {
    position: absolute; left: 0; width: 100%; top: 733px;
    text-align: center;
    font-family: "Mrs Saint Delafield", cursive;
    font-size: 62px; line-height: 1;
    letter-spacing: 4px; word-spacing: 18px;
  }
  .roast {
    position: absolute; left: 0; width: 100%; top: 792px;
    text-align: center;
    font-weight: 800; font-size: 12px; letter-spacing: 9px;
  }

  .info-box {
    position: absolute; left: 47px; top: 835px; width: 489px; height: 141px;
    border: 2.5px solid var(--ink);
    display: flex;
  }
  .details {
    width: 243px; border-right: 2.5px solid var(--ink);
    padding: 10px 0 0 16px;
    list-style: none; font-size: 11px; line-height: 17px;
  }
  .details b { font-weight: 800; }
  .format { flex: 1; display: flex; align-items: center; justify-content: center; gap: 10px; }
  .format-icon { width: 52px; height: 62px; }
  .format-text {
    font-family: "Josefin Sans", sans-serif; font-weight: 700;
    font-size: 31px; line-height: 0.95;
  }

  .footer {
    position: absolute; left: 50px; right: 46px; top: 1003px;
    display: flex; align-items: center; justify-content: space-between;
  }
  .social { display: flex; align-items: center; gap: 10px; font-weight: 800; font-size: 16px; }
  .social-dot { width: 44px; height: 44px; border-radius: 50%; background: var(--ink); }
  .weight { font-weight: 800; font-size: 14px; }
</style>
</head>
<body>
  <main class="label">
    <div class="colour-band" role="img" aria-label="Decorative band of vertical stripes in red, peach, green, yellow, blue and brown"></div>

    <svg class="badge" viewBox="0 0 246 246" aria-hidden="true">
      <circle cx="123" cy="123" r="123" fill="#ffffff"/>
      <circle cx="123" cy="123" r="104" fill="none" stroke="#9a4f12" stroke-width="7"/>
    </svg>
    <p class="badge-name">Copper Kettle Organic Coffee Roasters</p>

    <h1 class="title">BRAZILIAN ROAST</h1>
    <p class="tagline">smooth &amp; mellow</p>
    <p class="roast">AIR ROASTED MEDIUM</p>

    <section class="info-box">
      <ul class="details">
        <li><b>FLAVOUR NOTES:</b> Blackberry, vanilla</li>
        <li><b>PRODUCER:</b> Mateus Oliveira</li>
        <li><b>LOCATION:</b> Rio de Janeiro</li>
        <li><b>VARIETY:</b> Caturra</li>
        <li><b>ELEVATION:</b> 1500m</li>
        <li><b>PROCESS:</b> Natural</li>
        <li><b>ROAST DATE:</b> 23/10/2022</li>
      </ul>
      <div class="format">
        <svg class="format-icon" viewBox="0 0 52 62" role="img" aria-label="Icon of three coffee beans in green, red and brown">
          <rect width="52" height="62" rx="10" fill="#8b5a2f"/>
        </svg>
        <p class="format-text">WHOLE<br>BEAN</p>
      </div>
    </section>

    <footer class="footer">
      <div class="social"><span class="social-dot"></span>@CopperKettleRoasters</div>
      <p class="weight">Net Wt. 12oz (340gms)</p>
    </footer>
  </main>
</body>
</html>
```